Design my site www.brieflyledger.com

So here is what I am thinking in terms of design:

https://plenvo.com

https://www.skyluxair.com

http://kalvex.com/harbor-plaza-tower/

I want the theme to be white and blue (royal blue). I attached a paint picture of what I would like the site to look like in terms of placing the text. Generally, what I like about the sites above is that they are simple, you can navigate easily and have some kind of idea of what's going on by looking at the center (picture and motto). Let's establish a clear understanding of how the functional part of the site would look like. Please see the picture attached.

I want to keep it simple: On top would be the Name 'BRIEFLY ledger", somewhere to the right on top on the page would be 'Sign in" button.

In the center would be a picture (maybe a video) with the Motto (on top of it all in capital) OBSERVE NAVIGATE DECIDE and below would be the "sign up now"

Below the picture (like on kalvex.com site) or to the left on top of the page would be "About Us', "Press" "Contact Us' buttons.

Then once the user gets to his page his got 3 tabs " Press Headlines", "Events", " Briefings".

we would keep the same format I only have on the site, but separate for every Tab.

I do not want the user to get distracted. I also want him to be able to access the page though mobile phone and be able to get automatic updates just like Zorvan Pings without having to sign in daily.

The landing page must be minimalist yet with business/corporate feel where users can navigate easily and a "what you see is what you get" approach. You want an image or video (personally I prefer the video.. it does capture the users attention instantly, as long as it is an interesting video), with your taglines in it.

Sections available to public: About Us, Contact Us, Landing Page with Signup Option

Private: Public Sections + User Account Page, Tabs for (Events, Press Headlines, Briefings)

Target Market(s)

PR/media monitoring/diplomatic community

Coding

Coded - Design and coding required

Number of Pages Required

1 page

Font styles to use
Serif
Sans Serif

Colors
0255a3
ec1f27

Requirements
Must have
• a simple landing page, that is user friendly.
Nice to have
• a video with the explanation of how to navigate the site
Should not have
• too many colors, graphs etc.

```html
<!DOCTYPE html>
<html lang="en">
<head>
<meta charset="utf-8">
<title>BRIEFLY ledger – Press Headlines</title>
<link rel="stylesheet" href="https://fonts.googleapis.com/css2?family=Montserrat:wght@400;500&family=Open+Sans:ital,wght@0,400;0,700;1,400&family=Raleway:wght@400;500&display=swap">
<style>
  :root {
    --royal-blue: #0255a3;
    --alert-red: #ec1f27;
    --white: #ffffff;
    --ink: #2b2b2b;
    --meta-ink: #333333;
    --sky: #c9d6e0;
    --hills: #8f9a94;
    --city: #6f6a60;
    --sea: #4a9cc0;
    --shade: rgba(28, 40, 48, 0.72);
  }
  * { box-sizing: border-box; margin: 0; padding: 0; }
  html, body { width: 1200px; height: 518px; overflow: hidden; }
  body {
    position: relative;
    font-family: "Open Sans", Arial, sans-serif;
    color: var(--ink);
    background: var(--sky);
  }
  .backdrop { position: absolute; inset: 0; width: 1200px; height: 518px; display: block; }

  .site-header {
    position: absolute; top: 0; left: 0;
    width: 1200px; height: 70px;
    background: var(--royal-blue);
    color: var(--white);
  }
  .brand {
    position: absolute; left: 145px; top: 19px;
    font-family: "Montserrat", Arial, sans-serif;
    font-weight: 400; font-size: 23px; letter-spacing: 0.2px;
  }
  .account {
    position: absolute; right: 136px; top: 19px;
    display: flex; align-items: center; gap: 18px;
    font-family: "Raleway", Arial, sans-serif; font-size: 11px;
  }
  .avatar {
    width: 33px; height: 33px; border-radius: 3px;
    background: linear-gradient(180deg, #e9dccb 0%, #d8b894 100%);
  }

  .tabs {
    position: absolute; left: 162px; top: 87px;
    display: flex; height: 39px;
    font-family: "Montserrat", Arial, sans-serif; font-size: 13px;
  }
  .tab { display: flex; align-items: center; padding: 0 19px 0 20px; color: #222; }
  .tab.is-active { background: var(--royal-blue); color: var(--white); width: 136px; justify-content: center; padding: 0; }
  .tab-rule {
    position: absolute; left: 162px; top: 126px;
    width: 876px; height: 8px; background: var(--royal-blue);
  }

  .headline-card {
    position: absolute; left: 164px; top: 134px;
    width: 872px; height: 330px;
    background: var(--white);
    box-shadow: 0 3px 8px rgba(0,0,0,0.3);
    padding: 31px 28px 0 27px;
  }
  .meta { display: flex; align-items: center; font-size: 10.5px; height: 12px; }
  .meta svg { flex: none; }
  .meta-date { font-weight: 700; color: var(--royal-blue); margin-left: 10px; margin-right: 33px; }
  .meta-label { font-weight: 700; color: var(--royal-blue); margin-left: 11px; margin-right: 6px; }
  .meta-keywords { font-style: italic; color: var(--meta-ink); }
  .headline {
    margin-top: 17px;
    font-family: "Montserrat", Arial, sans-serif;
    font-weight: 400; font-size: 21.5px; line-height: 26px;
    color: var(--royal-blue);
  }
  .summary {
    margin-top: 8px;
    font-size: 10.6px; line-height: 19.2px;
    text-align: justify; color: var(--ink);
  }
  .summary + .summary { margin-top: 19px; }
  .read-more {
    display: inline-flex; align-items: center; justify-content: center;
    margin-top: 14px;
    width: 97px; height: 30px;
    background: var(--alert-red); color: var(--white);
    font-family: "Montserrat", Arial, sans-serif; font-size: 11px;
    text-decoration: none; box-shadow: 0 2px 4px rgba(0,0,0,0.3);
  }

  .copyright {
    position: absolute; left: 178px; top: 480px;
    font-family: "Raleway", Arial, sans-serif; font-size: 10px; color: var(--white);
  }
  .page-code {
    position: absolute; left: 1125px; top: 469px;
    font-family: "Raleway", Arial, sans-serif; font-size: 10.5px; color: var(--white);
  }
  .footer-band {
    position: absolute; left: 0; bottom: 0;
    width: 1200px; height: 6px; background: var(--alert-red);
  }
</style>
</head>
<body>
  <svg class="backdrop" viewBox="0 0 1200 518" role="img" aria-label="Photograph of a coastal city with high-rise towers, mountains and blue sea">
    <defs>
      <linearGradient id="scene-sky" x1="0" y1="0" x2="0" y2="1">
        <stop offset="0" stop-color="#cfdbe4"/>
        <stop offset="0.35" stop-color="#a9b3ae"/>
        <stop offset="1" stop-color="#7a7468"/>
      </linearGradient>
      <linearGradient id="scene-sea" x1="0" y1="0" x2="1" y2="0">
        <stop offset="0" stop-color="#8c8a80" stop-opacity="0"/>
        <stop offset="0.8" stop-color="#5fa6c6" stop-opacity="0"/>
        <stop offset="0.9" stop-color="#4f9fc3"/>
        <stop offset="1" stop-color="#3f95bd"/>
      </linearGradient>
    </defs>
    <rect width="1200" height="518" fill="url(#scene-sky)"/>
    <rect y="270" width="1200" height="248" fill="url(#scene-sea)"/>
    <polygon points="0,360 1200,430 1200,518 0,518" fill="var(--shade)"/>
  </svg>

  <header class="site-header">
    <div class="brand">BRIEFLY ledger</div>
    <div class="account">
      <span class="user-name">User name</span>
      <div class="avatar" role="img" aria-label="User profile picture"></div>
    </div>
  </header>

  <nav class="tabs">
    <span class="tab is-active">Press Headlines</span>
    <span class="tab">Events</span>
    <span class="tab">Daily Briefings</span>
  </nav>
  <div class="tab-rule"></div>

  <article class="headline-card">
    <div class="meta">
      <svg width="13" height="13" viewBox="0 0 13 13" aria-hidden="true">
        <rect x="0.5" y="2" width="12" height="10.5" fill="none" stroke="#0255a3"/>
        <rect x="0.5" y="2" width="12" height="2.5" fill="#0255a3"/>
        <rect x="3" y="0" width="1.5" height="3" fill="#0255a3"/>
        <rect x="8.5" y="0" width="1.5" height="3" fill="#0255a3"/>
        <g fill="#0255a3">
          <rect x="2" y="6" width="2" height="1.6"/><rect x="5.5" y="6" width="2" height="1.6"/><rect x="9" y="6" width="2" height="1.6"/>
          <rect x="2" y="9" width="2" height="1.6"/><rect x="5.5" y="9" width="2" height="1.6"/><rect x="9" y="9" width="2" height="1.6"/>
        </g>
      </svg>
      <span class="meta-date">12-June-2016</span>
      <svg width="9" height="12" viewBox="0 0 9 12" aria-hidden="true">
        <path d="M0 0H9V12L4.5 8.5L0 12Z" fill="#0255a3"/>
      </svg>
      <span class="meta-label">Keywords :</span>
      <span class="meta-keywords">Lorium ipsum,&nbsp; Dolor Amit,&nbsp; Adipising, Design, Printing....</span>
    </div>
    <h1 class="headline">Condimentum vivamus tellus vel adipiscing dignissim</h1>
    <p class="summary">Venenatis blandit suspendisse proin mi id malesuada consectetur per diam nibh leo vivamus nec eu proin nisl suspendisse volutpat vestibulum duis condimentum a vivamus nibh eros torquent adipiscing condimentum.Morbi suspendisse et class enim vehicula adipiscing ultrices purus a cum inceptos potenti.</p>
    <p class="summary">Imperdiet a orci ultrices a duis vestibulum hendrerit penatibus donec rhoncus phasellus scelerisque lacinia a a adipiscing neque suspendisse a lacinia erat a in.Dis cum aliquet dictumst vel penatibus amet aliquet parturient sociis consequat velit leo nibh parturient faucibus facilisis odio vulputate ipsum a dolor imperdiet suspendisse a adipiscing. Sem adipiscing proin netus malesuada per sed ridiculus hendrerit eget a at convallis ad a imperdiet vel potenti scelerisque pharetra nascetur risus facilisis senectus ultricies et ac adipiscing.</p>
    <a class="read-more" href="#">READ MORE</a>
  </article>

  <footer>
    <div class="copyright">© 2016 . www.brieflyledger.com</div>
    <div class="page-code">M1</div>
    <div class="footer-band"></div>
  </footer>
</body>
</html>
```